Modern Business Card

Modern professional business card with more than just logo and demographic info. Something memorable.

We are a trendy/modern chiropractic group with an emphasis on neurology, hence the minimalist-type brain logo. We want to convey that modern and technical aspect with professionalism and the elite nature of our practice environment.

```html
<!DOCTYPE html>
<html lang="en">
<head>
<meta charset="utf-8">
<title>Keystone Chiropractic – Business Card</title>
<link rel="stylesheet" href="https://fonts.googleapis.com/css2?family=Cinzel:wght@400;600&family=Crimson+Text:wght@400&display=swap">
<style>
  :root {
    --bg: #d9d9db;
    --card-white: #ffffff;
    --card-black: #151515;
    --brand-blue: #3d74c0;
    --edge-blue: #2c5aa0;
    --ink: #1d1d1d;
    --ink-soft: #3a3a3a;
    --white: #ffffff;
  }
  * { box-sizing: border-box; margin: 0; padding: 0; }
  html, body { width: 1200px; height: 800px; overflow: hidden; }
  body {
    background: var(--bg);
    display: flex;
    align-items: center;
    justify-content: center;
    gap: 40px;
    font-family: "Crimson Text", Georgia, serif;
  }
  .card {
    position: relative;
    width: 540px;
    height: 310px;
    border-radius: 22px;
    box-shadow: 0 3px 0 var(--edge-blue), 0 14px 30px rgba(0,0,0,0.18);
    overflow: hidden;
  }

  /* Front */
  .card--front { background: var(--card-white); }
  .front__brand {
    position: absolute;
    top: 44px;
    right: 44px;
    display: flex;
    flex-direction: column;
    align-items: center;
    gap: 16px;
  }
  .front__brand-dot {
    width: 120px;
    height: 120px;
    border-radius: 50%;
    background: var(--brand-blue);
  }
  .front__brand-name {
    font-family: "Cinzel", "Times New Roman", serif;
    font-weight: 400;
    font-size: 22px;
    letter-spacing: 2px;
    color: var(--brand-blue);
  }
  .front__details {
    position: absolute;
    left: 38px;
    bottom: 28px;
  }
  .person__name {
    font-family: "Cinzel", "Times New Roman", serif;
    font-weight: 400;
    font-size: 21px;
    letter-spacing: 1px;
    color: var(--brand-blue);
    line-height: 1;
  }
  .person__role {
    font-family: "Cinzel", "Times New Roman", serif;
    font-weight: 600;
    font-size: 11px;
    letter-spacing: 1.5px;
    color: var(--ink);
    margin-top: 4px;
  }
  .address {
    font-style: normal;
    font-size: 13px;
    line-height: 1.2;
    color: var(--ink-soft);
    margin-top: 14px;
  }
  .contact-list {
    list-style: none;
    margin-top: 10px;
    font-size: 13px;
    line-height: 1.25;
    color: var(--ink-soft);
  }
  .contact-list li { display: flex; align-items: center; gap: 8px; }
  .contact-list svg { width: 11px; height: 11px; fill: var(--brand-blue); flex: none; }

  /* Back */
  .card--back {
    background: var(--card-black);
    display: flex;
    align-items: center;
    justify-content: center;
  }
  .back__brand { display: flex; align-items: center; gap: 22px; }
  .back__brand-dot {
    width: 74px;
    height: 74px;
    border-radius: 50%;
    background: var(--brand-blue);
  }
  .back__brand-name {
    font-family: "Cinzel", "Times New Roman", serif;
    font-weight: 400;
    color: var(--white);
    line-height: 0.95;
  }
  .back__brand-line1 { display: block; font-size: 52px; letter-spacing: 1px; }
  .back__brand-line2 { display: block; font-size: 25px; letter-spacing: 1px; }
</style>
</head>
<body>

  <section class="card card--front" aria-label="Card front">
    <div class="front__brand">
      <div class="front__brand-dot"></div>
      <div class="front__brand-name">Keystone</div>
    </div>

    <div class="front__details">
      <h1 class="person__name">Daniel Harper</h1>
      <p class="person__role">President</p>
      <address class="address">1420 Birchwood Road<br>Juneau, Alaska 99801</address>
      <ul class="contact-list">
        <li>
          <svg viewBox="0 0 12 12" aria-hidden="true"><path d="M2.5 1 L4.5 1 L5.2 3.6 L4 4.6 Q5 7 7.4 8 L8.4 6.8 L11 7.5 L11 9.5 Q10.5 11 9 11 Q1 10 1 2.5 Q1 1.2 2.5 1 Z"/></svg>
          555-210-4417
        </li>
        <li>
          <svg viewBox="0 0 12 12" aria-hidden="true"><path d="M3 0.5 H9 Q10 0.5 10 1.5 V10.5 Q10 11.5 9 11.5 H3 Q2 11.5 2 10.5 V1.5 Q2 0.5 3 0.5 Z M3.3 1.8 V9 H8.7 V1.8 Z"/></svg>
          555-318-6042
        </li>
        <li>
          <svg viewBox="0 0 12 12" aria-hidden="true"><path d="M3 0.5 H8 V4 H3 Z M1 4.5 H11 V11 H1 Z M3 6.5 V7.5 H9 V6.5 Z"/></svg>
          555-472-9135
        </li>
        <li>
          <svg viewBox="0 0 12 12" aria-hidden="true"><path d="M0.5 2 H11.5 V10 H0.5 Z M1.2 2.8 L6 6.5 L10.8 2.8 Z"/></svg>
          name@keystonechiropractic.com
        </li>
        <li>
          <svg viewBox="0 0 12 12" aria-hidden="true"><path d="M6 0.5 A5.5 5.5 0 1 0 6.01 0.5 Z M6 2 A4 4 0 0 1 6 10 A4 4 0 0 1 6 2 Z M2 6 H10 V6.8 H2 Z M5.6 2 H6.4 V10 H5.6 Z"/></svg>
          www.keystonechiropractic.com
        </li>
      </ul>
    </div>
  </section>

  <section class="card card--back" aria-label="Card back">
    <div class="back__brand">
      <div class="back__brand-dot"></div>
      <div class="back__brand-name">
        <span class="back__brand-line1">KEYSTONE</span>
        <span class="back__brand-line2">CHIROPRACTIC</span>
      </div>
    </div>
  </section>

</body>
</html>
```